Marta's Dwellings website

We need a simple website for our property investment business in the UK. We basically need our contact details and brief description.We have the company logo already done (via ArtFlockly) so please use these:https://drive.google.com/drive/folders/1szJ3iRhelElZ40NIFT7w-c14MaY3Y_oV?usp=sharingYou could use some stock photos of UK houses for now.Let me know when to provide more detailed descriptions, etc

Coding

Coded - Design and coding required

Number of Pages Required

1 page

Colors

Designer to choose colors to be used in the design.

```html
<!DOCTYPE html>
<html lang="en">
<head>
<meta charset="utf-8">
<title>Marta's Dwellings</title>
<link href="https://fonts.googleapis.com/css2?family=Montserrat:wght@400;500;600;700&family=Lato:wght@400;700&display=swap" rel="stylesheet">
<style>
:root{
  --blue:#29a8e0;
  --ink:#1e1e1e;
  --text:#333;
  --grey:#ebebeb;
  --dark:#2b2d33;
  --white:#fff;
}
*{box-sizing:border-box;margin:0;padding:0}
html,body{width:1200px;height:3801px;overflow:hidden}
body{position:relative;background:var(--white);font-family:'Lato',sans-serif;color:var(--text)}
.abs{position:absolute}
.head{font-family:'Montserrat',sans-serif}
.btn{position:absolute;background:var(--blue);color:#fff;font-family:'Lato',sans-serif;font-size:15px;display:flex;align-items:center;justify-content:center;border-radius:4px}
/* header */
.brand{left:120px;top:125px;font-family:'Montserrat',sans-serif;font-size:19px;letter-spacing:9px;color:var(--ink);font-weight:500}
.brand-mark{left:218px;top:28px;width:92px;height:90px;background:var(--ink)}
.nav{top:32px;font-family:'Montserrat',sans-serif;font-size:18px;color:var(--ink)}
.contact-top{right:140px;font-family:'Lato',sans-serif;font-size:19px;color:var(--blue)}
/* hero */
.hero{left:0;top:166px;width:1200px;height:586px;background:linear-gradient(180deg,#3e4a66 0%,#4b5673 45%,#5b6a3e 75%,#3f6e2a 100%)}
.hero-peak{left:0;top:80px}
.hero-title{left:0;width:1200px;top:378px;text-align:center;color:#fff;font-family:'Montserrat',sans-serif;font-weight:600;font-size:60px;line-height:72px}
.hero-box{left:270px;top:378px;width:650px;height:170px;background:rgba(20,20,25,.45)}
.arrow{width:34px;height:34px;border-radius:50%;background:var(--blue)}
/* about */
.section-title{font-family:'Montserrat',sans-serif;font-weight:600;color:var(--ink)}
.para{font-size:13px;line-height:30px;color:#333}
/* projects */
.projects{left:0;top:1270px;width:1200px;height:805px;background:linear-gradient(180deg,#2e3038 0%,#3a3d44 50%,#3c4a30 100%)}
.card{position:absolute;top:1464px;width:306px;height:466px;background:#fff}
.card .pic{height:243px}
.card h3{font-family:'Montserrat',sans-serif;font-weight:500;font-size:26px;color:#222;margin:24px 0 0 24px}
.card p{font-family:'Montserrat',sans-serif;font-size:15px;line-height:21px;color:#333;margin:16px 24px 0 27px}
.card .btn{left:85px;top:400px;width:136px;height:44px}
.dot{width:19px;height:19px;border-radius:50%;background:#fff;top:1991px}
/* features */
.features{left:111px;top:2527px;width:730px;height:157px;background:#fff;border:1px solid #ddd}
.feat{font-family:'Montserrat',sans-serif;font-weight:500;font-size:17px;color:#222}
/* blog */
.blog{left:0;top:2772px;width:1200px;height:525px;background:var(--grey)}
.post-pic{top:2912px;width:312px;height:200px}
.date{background:var(--blue);color:#fff;font-family:'Montserrat',sans-serif;font-weight:600;font-size:14px;display:flex;align-items:center;justify-content:center;width:108px;height:36px}
.post-title{font-family:'Montserrat',sans-serif;font-weight:500;font-size:30px;color:#333;width:312px;text-align:center;top:3138px}
.post-text{width:312px;text-align:center;font-size:13px;line-height:30px;color:#444;top:3190px}
.post-text a{color:var(--blue)}
/* footer */
.footer{left:0;top:3297px;width:1200px;height:453px;background:var(--blue);color:#fff}
.foot-h{font-family:'Montserrat',sans-serif;font-weight:500;font-size:20px;color:#e8f6fd}
.foot-link{font-family:'Montserrat',sans-serif;font-size:14px;letter-spacing:1.5px;color:#fff}
.foot-txt{font-size:14px;line-height:22px;color:#fff}
.ico{width:18px;height:18px;border-radius:50%;background:#fff}
.bottom{left:111px;top:3764px;font-family:Arial,sans-serif;font-size:13px;color:#333}
</style>
</head>
<body>

<!-- header -->
<div class="abs brand">MARTA'S DWELLINGS</div>
<div class="abs nav" style="left:391px">Home</div>
<div class="abs nav" style="left:493px">About Us</div>
<div class="abs nav" style="left:621px">Projects</div>
<div class="abs nav" style="left:734px">Our Properties</div>
<div class="abs nav" style="left:906px">Blog</div>
<div class="abs nav" style="left:989px">Contact Us</div>
<div class="abs contact-top" style="top:85px;right:160px">(555) 014 2273</div>
<svg class="abs" style="left:1066px;top:84px" width="26" height="26" viewBox="0 0 24 24"><path fill="#222" d="M6.6 10.8c1.4 2.8 3.8 5.1 6.6 6.6l2.2-2.2c.3-.3.7-.4 1-.2 1.1.4 2.3.6 3.6.6.6 0 1 .4 1 1V20c0 .6-.4 1-1 1C10.6 21 3 13.4 3 4c0-.6.4-1 1-1h3.5c.6 0 1 .4 1 1 0 1.3.2 2.5.6 3.6.1.3 0 .7-.2 1z"/></svg>
<div class="abs contact-top" style="top:127px;right:160px">hello@martasdwell.com</div>
<svg class="abs" style="left:1062px;top:131px" width="30" height="22" viewBox="0 0 30 22"><rect x="1" y="1" width="28" height="20" fill="none" stroke="#222" stroke-width="2"/><path d="M1 1l14 11L29 1M1 21l10-10M29 21L19 11" fill="none" stroke="#222" stroke-width="2"/></svg>

<!-- hero -->
<div class="abs hero" role="img" aria-label="Photo of a blue clapboard family house with a porch, lawn and trees"></div>
<svg class="abs" style="left:460px;top:80px" width="272" height="88" viewBox="0 0 272 88"><polygon points="0,88 136,0 272,88" fill="#4d5a7c"/></svg>
<div class="abs hero-box"></div>
<div class="abs hero-title">Welcome To<br>MARTA'S DWELLINGS</div>
<svg class="abs" style="left:60px;top:465px" width="34" height="34" viewBox="0 0 34 34"><circle cx="17" cy="17" r="17" fill="#29a8e0"/><path d="M23 17H11m5-6l-6 6 6 6" stroke="#fff" stroke-width="2.5" fill="none"/></svg>
<svg class="abs" style="left:1103px;top:465px" width="34" height="34" viewBox="0 0 34 34"><circle cx="17" cy="17" r="17" fill="#29a8e0"/><path d="M11 17h12m-5-6l6 6-6 6" stroke="#fff" stroke-width="2.5" fill="none"/></svg>

<!-- about -->
<div class="abs section-title" style="left:113px;top:820px;font-size:42px">About Us</div>
<p class="abs para" style="left:113px;top:885px;width:540px">Lorem ipsum dolor sit amet, consectetur adipiscing elit, sed do eiusmod tempor incididunt ut labore et dolore magna aliqua. Quis ipsum suspendisse ultrices gravida. Risus commodo viverra maecenas accumsan lacus vel facilisis. Lorem ipsum dolor sit amet, consectetur adipiscing elit, sed do eiusmod tempor incididunt ut labore et dolore magna aliqua. Quis ipsum suspendisse ultrices gravida. Risus commodo viverra maecenas accumsan lacus vel facilisis. sed do eiusmod tempor incididunt ut labore et dolore magna aliqua. Quis ipsum suspendisse ultrices gravida. Risus commodo viverra maecenas accumsan lacus vel facili-</p>
<div class="btn" style="left:110px;top:1124px;width:118px;height:42px">Read more</div>
<svg class="abs" style="left:710px;top:785px" width="390" height="390" viewBox="0 0 390 390">
  <path d="M345 75 A185 185 0 0 0 40 140" fill="none" stroke="#29a8e0" stroke-width="9"/>
  <path d="M30 180 A165 165 0 0 0 175 360" fill="none" stroke="#29a8e0" stroke-width="10"/>
  <path d="M380 190 A185 185 0 0 1 230 380" fill="none" stroke="#29a8e0" stroke-width="8"/>
</svg>
<div class="abs" role="img" aria-label="Photo of a red brick Tudor-style detached house with garden" style="left:742px;top:818px;width:326px;height:326px;border-radius:50%;background:radial-gradient(circle at 50% 40%,#b9d6ee 0%,#a2533c 45%,#6b8f3a 85%)"></div>

<!-- projects -->
<div class="abs projects" role="img" aria-label="Dark background photo of a house at dusk"></div>
<div class="abs section-title" style="left:0;width:1200px;text-align:center;top:1338px;font-size:42px;color:#fff">Projects</div>

<div class="card" style="left:111px"><div class="pic" role="img" aria-label="Photo of a suburban street with houses and trees" style="background:linear-gradient(180deg,#7aa24a,#8fa3b8 60%,#7d8b6a)"></div><h3>Lorem Ipsum</h3><p>Lorem ipsum dolor sit amet, consectetur adipiscing elit, sed do eiusmod tempor</p><div class="btn">Read More</div></div>
<div class="card" style="left:446px"><div class="pic" role="img" aria-label="Photo of a large stone manor house with lawn" style="background:linear-gradient(180deg,#d9e3ec,#c9b89a 55%,#7fae3a)"></div><h3>Lorem Ipsum</h3><p>Lorem ipsum dolor sit amet, consectetur adipiscing elit, sed do eiusmod tempor</p><div class="btn">Read More</div></div>
<div class="card" style="left:782px"><div class="pic" role="img" aria-label="Photo of a yellow house with front steps and lawn" style="background:linear-gradient(180deg,#dfe9f2,#e0c98a 50%,#6fa83a)"></div><h3>Lorem Ipsum</h3><p>Lorem ipsum dolor sit amet, consectetur adipiscing elit, sed do eiusmod tempor</p><div class="btn">Read More</div></div>

<div class="abs dot" style="left:559px;background:none;border:2px solid #fff"></div>
<div class="abs dot" style="left:589px"></div>
<div class="abs dot" style="left:619px"></div>

<!-- like our work -->
<div class="abs section-title" style="left:109px;top:2230px;font-size:42px">Like Our Work?</div>
<p class="abs para" style="left:113px;top:2300px;width:480px;font-size:14px">Lorem ipsum dolor sit amet, consectetur adipiscing elit, sed do eiusmod tempor incididunt ut labore et dolore magna aliqua. Quis ipsum suspendisse ultrices gravida. Risus commodo viverra maecenas accumsan lacus vel facilisis.</p>
<div class="btn" style="left:118px;top:2445px;width:118px;height:42px">Read more</div>
<div class="abs" role="img" aria-label="Photo of a row of British terraced houses under a cloudy sky" style="left:600px;top:2195px;width:489px;height:488px;background:linear-gradient(160deg,#8fb8e0 0%,#dfe7ef 35%,#b56b4e 60%,#d2b47a 80%,#5b7d3a 100%)"></div>
<div class="abs features"></div>
<svg class="abs" style="left:153px;top:2560px" width="82" height="80" viewBox="0 0 82 80" fill="none" stroke="#29a8e0" stroke-width="2"><path d="M4 12v58l8 8h60l-8-8H12"/><path d="M4 12l8 6v52"/><path d="M30 50l40-40 6 6-40 40-9 3z"/><path d="M48 74V56l-14 18"/><rect x="55" y="60" width="14" height="14"/></svg>
<div class="abs feat" style="left:252px;top:2592px">House Unite</div>
<svg class="abs" style="left:396px;top:2560px" width="72" height="76" viewBox="0 0 72 76" fill="none" stroke="#333" stroke-width="2"><circle cx="16" cy="18" r="12"/><circle cx="36" cy="14" r="12"/><circle cx="56" cy="20" r="12"/><path d="M16 30v26M36 26v30M56 32v24"/><path d="M2 58c10-6 20 6 34 0s24 6 34 0M2 68c10-6 20 6 34 0s24 6 34 0" stroke="#29a8e0"/></svg>
<div class="abs feat" style="left:483px;top:2592px">Green Area</div>
<svg class="abs" style="left:628px;top:2562px" width="66" height="70" viewBox="0 0 66 70" fill="none" stroke="#29a8e0" stroke-width="2"><path d="M4 20L33 4l29 16v48H4z"/><rect x="12" y="26" width="10" height="12"/><rect x="44" y="26" width="10" height="12"/><rect x="28" y="22" width="10" height="10"/><rect x="27" y="48" width="12" height="20"/><rect x="10" y="48" width="10" height="10"/><rect x="46" y="48" width="10" height="10"/></svg>
<div class="abs feat" style="left:716px;top:2592px">Home</div>

<!-- blog -->
<div class="abs blog"></div>
<div class="abs section-title" style="left:0;width:1200px;text-align:center;top:2830px;font-size:40px;font-weight:500">Our Blog</div>
<svg class="abs" style="left:52px;top:3010px" width="30" height="30" viewBox="0 0 34 34"><circle cx="17" cy="17" r="17" fill="#29a8e0"/><path d="M23 17H11m5-6l-6 6 6 6" stroke="#fff" stroke-width="2.5" fill="none"/></svg>
<svg class="abs" style="left:1124px;top:2998px" width="30" height="30" viewBox="0 0 34 34"><circle cx="17" cy="17" r="17" fill="#29a8e0"/><path d="M11 17h12m-5-6l6 6-6 6" stroke="#fff" stroke-width="2.5" fill="none"/></svg>

<div class="abs post-pic" role="img" aria-label="Photo of a brick house with a glass conservatory" style="left:113px;background:linear-gradient(180deg,#c9d9ea,#a86a52 55%,#8c6a4a)"></div>
<div class="abs date" style="left:311px;top:3076px">Apr 24 2019</div>
<div class="abs post-pic" role="img" aria-label="Photo of red brick semi-detached houses with trees" style="left:442px;background:linear-gradient(180deg,#dbe5ee,#9a5a44 50%,#5d6b3c)"></div>
<div class="abs date" style="left:640px;top:3076px">Apr 08 2019</div>
<div class="abs post-pic" role="img" aria-label="Photo of a terrace of Tudor-style brick houses" style="left:776px;background:linear-gradient(180deg,#d7e2ee,#a44a3a 50%,#6d5a52)"></div>
<div class="abs date" style="left:977px;top:3076px">Apr 08 2019</div>

<div class="abs post-title" style="left:113px">Lorem Ipsum</div>
<div class="abs post-title" style="left:442px">Lorem Ipsum</div>
<div class="abs post-title" style="left:776px">Lorem Ipsum</div>
<div class="abs post-text" style="left:113px">Lorem ipsum dolor sit amet,<br>adipiscing elit, <a>Read More</a></div>
<div class="abs post-text" style="left:442px">Lorem ipsum dolor sit amet,<br>adipiscing elit, <a>Read More</a></div>
<div class="abs post-text" style="left:776px">Lorem ipsum dolor sit amet,<br>adipiscing elit, <a>Read More</a></div>

<!-- footer -->
<div class="abs footer"></div>
<div class="abs" style="left:131px;top:3408px;font-family:'Montserrat',sans-serif;font-size:15px;letter-spacing:6px;color:#fff;font-weight:500">MARTA'S DWELLINGS</div>
<svg class="abs" style="left:132px;top:3468px" width="18" height="24" viewBox="0 0 18 24"><path d="M9 0a9 9 0 0 0-9 9c0 7 9 15 9 15s9-8 9-15a9 9 0 0 0-9-9zm0 13a4 4 0 1 1 0-8 4 4 0 0 1 0 8z" fill="#fff"/></svg>
<div class="abs foot-txt" style="left:166px;top:3464px">Unit 7,<br>Harbour Court,<br>12-14 Willow Row,<br>Ashby Vale,<br>Derbyshire,<br>United Kingdom, DE74 9QX</div>
<svg class="abs" style="left:132px;top:3622px" width="20" height="20" viewBox="0 0 24 24"><path fill="#fff" d="M6.6 10.8c1.4 2.8 3.8 5.1 6.6 6.6l2.2-2.2c.3-.3.7-.4 1-.2 1.1.4 2.3.6 3.6.6.6 0 1 .4 1 1V20c0 .6-.4 1-1 1C10.6 21 3 13.4 3 4c0-.6.4-1 1-1h3.5c.6 0 1 .4 1 1 0 1.3.2 2.5.6 3.6.1.3 0 .7-.2 1z"/></svg>
<div class="abs foot-txt" style="left:177px;top:3620px">(555) 014 2273</div>
<svg class="abs" style="left:132px;top:3673px" width="22" height="16" viewBox="0 0 30 22"><rect x="1" y="1" width="28" height="20" fill="none" stroke="#fff" stroke-width="2"/><path d="M1 1l14 11L29 1" fill="none" stroke="#fff" stroke-width="2"/></svg>
<div class="abs foot-txt" style="left:174px;top:3668px">hello@martasdwell.com</div>

<div class="abs foot-h" style="left:431px;top:3362px">Quick Links</div>
<div class="abs foot-link" style="left:433px;top:3415px;line-height:31px">Home<br>About Us<br>Our Properties<br>Blog<br>Contact Us</div>

<div class="abs foot-h" style="left:632px;top:3362px">Social Media</div>
<div class="abs ico" style="left:639px;top:3424px"></div><div class="abs foot-link" style="left:682px;top:3423px">Friendbook</div>
<div class="abs ico" style="left:639px;top:3476px"></div><div class="abs foot-link" style="left:682px;top:3475px">Chirper</div>
<div class="abs ico" style="left:639px;top:3521px"></div><div class="abs foot-link" style="left:682px;top:3520px">Globe plus</div>
<div class="abs ico" style="left:639px;top:3573px"></div><div class="abs foot-link" style="left:682px;top:3572px">Pinboardly</div>
<div class="abs ico" style="left:639px;top:3629px"></div><div class="abs foot-link" style="left:682px;top:3628px">Linkwork</div>

<div class="abs foot-h" style="left:849px;top:3362px">Newsletter</div>
<div class="abs" style="left:850px;top:3421px;width:229px;height:33px;border:1px solid #fff;font-size:13px;color:#fff;padding:8px 0 0 22px">Enter Email</div>
<div class="abs" style="left:853px;top:3475px;width:104px;height:25px;background:#fff;color:var(--blue);font-family:'Montserrat',sans-serif;font-size:10px;display:flex;align-items:center;justify-content:center">SUBSCRIBE</div>

<div class="abs bottom">© 2019 All Rights Reserved | Privacy Policy | Terms and Conditions</div>

</body>
</html>
```